Remodeling brochure

We need an informative homeowner friendly brochure detailing our company and things we do. We are looking for an initial setup and ideas (# of pages, etc) and then we will send more content. We are uploading our logo design. We are a high end remodeling company specializing in kitchen & bath remodels. We sell ourselves on customer communication and attention to detail in our designs and remodels.

Target Market(s)

Residential homeowners

Contact Information for Business Card

Modern and attention grabbing

Requirements
Must have
• Name- Hearth & Tile Works<br/>Address- 718 NW Larkfield Drive Suite #207<br/> Ankeny, Iowa 50099<br/>Phone- 515-555-0184<br/>email-htworksiowa@example-mail.com

```html
<!DOCTYPE html>
<html lang="en">
<head>
<meta charset="utf-8">
<title>Hearth &amp; Tile Works — Brochure Cover</title>
<link href="https://fonts.googleapis.com/css2?family=Montserrat:wght@300;400;600;800&display=swap" rel="stylesheet">
<style>
  :root {
    --backdrop: #e6e7e9;
    --paper: #ffffff;
    --brand-blue: #1565c8;
    --band-start: #2f8fd8;
    --band-end: #0d4fc0;
    --photo-light: #ece9e4;
    --photo-mid: #cfc7bb;
    --photo-warm: #b9a58c;
    --ink: #2b2f36;
  }
  * { box-sizing: border-box; margin: 0; padding: 0; }
  html, body { width: 1200px; height: 790px; overflow: hidden; }
  body {
    background: var(--backdrop);
    font-family: "Montserrat", sans-serif;
    display: flex;
    align-items: center;
    justify-content: center;
  }
  .cover {
    position: relative;
    width: 524px;
    height: 740px;
    background: var(--paper);
    box-shadow: 0 6px 24px rgba(0,0,0,0.18);
    overflow: hidden;
  }
  .brand {
    position: absolute;
    top: 52px;
    left: 0;
    right: 0;
    display: flex;
    align-items: center;
    justify-content: center;
    gap: 12px;
  }
  .brand-square {
    width: 34px;
    height: 34px;
    background: var(--brand-blue);
  }
  .brand-name {
    font-weight: 600;
    font-size: 24px;
    color: var(--brand-blue);
    letter-spacing: 0.01em;
  }
  .cover-photo {
    position: absolute;
    top: 128px;
    left: 0;
    width: 100%;
    height: 450px;
    background:
      linear-gradient(180deg, rgba(255,255,255,0.35) 0%, rgba(255,255,255,0) 40%),
      linear-gradient(100deg, var(--photo-mid) 0%, var(--photo-light) 35%, #f4f2ee 55%, var(--photo-mid) 80%, var(--photo-warm) 100%);
  }
  .feature-band {
    position: absolute;
    top: 548px;
    left: 0;
    width: 100%;
    height: 96px;
    background: linear-gradient(90deg, var(--band-start), var(--band-end));
    color: #fff;
    text-align: center;
    display: flex;
    flex-direction: column;
    justify-content: center;
    gap: 6px;
  }
  .feature-title {
    font-weight: 800;
    font-size: 25px;
    letter-spacing: 0.12em;
  }
  .feature-sub {
    font-weight: 300;
    font-size: 17px;
    letter-spacing: 0.06em;
  }
  .web-address {
    position: absolute;
    top: 680px;
    left: 0;
    right: 0;
    text-align: center;
    font-weight: 400;
    font-size: 11px;
    letter-spacing: 0.35em;
    color: var(--ink);
  }
</style>
</head>
<body>
  <main class="cover">
    <header class="brand">
      <span class="brand-square"></span>
      <span class="brand-name">Hearth &amp; Tile Works</span>
    </header>
    <div class="cover-photo" role="img" aria-label="Photo of a bright remodeled kitchen with marble island, brass faucet, pendant lights and large garden windows"></div>
    <section class="feature-band">
      <p class="feature-title">WE SPECIALIZE IN</p>
      <p class="feature-sub">KITCHEN AND BATHROOM RENOVATIONS</p>
    </section>
    <p class="web-address">www.htworksiowa.com</p>
  </main>
</body>
</html>
```